A4 Tri-fold Brochure for Sedation Dentist Specialist Dr. Marlon and Sedation Dentistry.

I would like to create an A4 tri-fold brochure for our Dental Sedation Specialist Dr. Marlon Duque. Please carefully select the most suitable highlights from his bio below.

This brochure has two parts. Highlighting what makes Dr. Marlon Duque unique and trustworthy. Include a picture of him (attached). The second part is about sedation dentistry. All you need to know here: http://www.calmchairhub.example/what-is-calm-chair-care

Avoid making it too wordy.

Meet Dr. Roel Benet Marlon Duque, DDS

Inspired to Become a Dentist:
As a child, Dr. Marlon Duque always felt stressed whenever he had to see a dentist. He knew that he wanted to become a dentist to help put patients completely at ease while they experienced quality dental care.

He is passionate about giving patients the healthy, beautiful smiles they deserve. “I find it fulfilling when I can see my patients’ beautiful smiles and how they can finally appreciate the joy of eating with a healthy set of teeth. However, what I love most about my job is the ability to provide a stress-free and comfortable experience at the dentist’s office, particularly for children, through sedation and general anesthesia.”

Educational Achievements:
Before becoming a dentist, Dr. Marlon Duque earned his undergraduate degree at the Northvale Institute of Arts where he received a Bachelor of Medical Science Honor Specialization degree with distinction in biochemistry. He then completed his Doctor of Dental Surgery degree with honors at the Kestrel Bay College. While there, he received the Linnet Orr Award in his class for outstanding achievement in anesthesia. He then pursued his three-year residency as well as a master’s degree in dental anesthesia at the Kestrel Bay College.

So he can provide his patients with the latest in dentistry, Dr. Marlon Duque enjoys pursuing additional knowledge, particularly in the areas of dental anesthesia as well as advanced technologies in dentistry. He is currently part of the Bright Arc study circle and has enrolled in the Core Anchor Short- Fellowship Course. He also serves as a clinical instructor at the Halvex Wing at the Kestrel Bay College.

Association Memberships:
In addition to his academic credentials, Dr. Marlon Duque is a member of several associations:
The Fenwick Board of Oral Practitioners of Ontario (FBOPO)
Dental Meridian Guild of Oral Sleep Care (MGOSC)
Northern Circle of Oral Calm Care (NCOCC)
Pellham Dental Alliance (PDA)
Outside the Practice

When he’s not at the practice, Dr. Marlon Duque enjoys spending time with his wife Dorla and their two poodles Pippa and Bramble, who are spoiled rotten! “Dorla and I love taking our dogs out on hikes and to the dog park on weekends. I also enjoy a wide range of activities from model building and playing the piano to soccer, gym and archery.” He stays fit by working out at the local Fitwell gym, and he likes to walk in Marrow Creek Park and Ashbury Field Park.

Dr. Marlon Duque considers himself to be a kid at heart. He is a big fan of superheroes and animated movies. “I get really excited about any upcoming superhero or Vellum Spark movies. Till this day, I still collect superhero toy figures.”

He supports the BrightWard Fund as well as the Lakeshore League for Animal Welfare and Rescue (LLAWR).

Experience outstanding dental care with our highly skilled dentist. Contact us today to schedule an appointment with Dr. Marlon Duque! He speaks English, Cantonese, and Mandarin.

Target Market(s)

Mothers with young kids.

Industry/Entity Type

Dental

Font styles to use
Sans Serif

Requirements
Should not have
• Prices

```html
<!DOCTYPE html>
<html lang="en">
<head>
<meta charset="utf-8">
<title>Sleep Dentistry – Tri-fold Brochure</title>
<link href="https://fonts.googleapis.com/css2?family=Mulish:wght@300;400;600;700;800&family=Montserrat:wght@700;800&display=swap" rel="stylesheet">
<style>
  :root{
    --blue:#1f9ad8;
    --blue-deep:#1666ad;
    --green:#5ed39b;
    --green-soft:#9ee8c2;
    --ink:#4f5559;
    --paper:#ffffff;
    --backdrop:#3a3a3c;
    --photo-skin:#d9c3b5;
    --photo-navy:#2a3a5c;
  }
  *{box-sizing:border-box;margin:0;padding:0}
  html,body{width:800px;height:1200px;overflow:hidden}
  body{background:var(--backdrop);font-family:"Mulish",sans-serif;color:var(--ink);position:relative}
  .sheet{position:absolute;left:50px;width:700px;height:496px;background:var(--paper);overflow:hidden;box-shadow:0 6px 18px rgba(0,0,0,.45)}
  .sheet--outside{top:83px}
  .sheet--inside{top:642px}
  .sheet-art{position:absolute;inset:0;width:700px;height:496px}
  .block{position:absolute}
  .body-text{font-size:8.4px;line-height:11.4px;text-align:justify}
  .body-text p+p{margin-top:9px}

  /* outside sheet */
  .memberships{left:25px;top:28px;width:200px}
  .memberships h2{font-weight:400;font-size:16px;color:var(--blue-deep);white-space:nowrap}
  .memberships .intro{font-size:7.2px;line-height:9.4px;margin-top:10px;color:#333}
  .memberships ul{list-style:none;margin-top:17px}
  .memberships li{position:relative;padding-left:16px;font-size:9.4px;line-height:12.2px;color:var(--blue-deep);margin-bottom:8px}
  .memberships li svg{position:absolute;left:0;top:2px;width:9px;height:9px}
  .phone{left:33px;top:458px;display:flex;align-items:center;gap:6px;color:#fff;font-family:"Montserrat",sans-serif;font-weight:800;font-size:18px}
  .phone svg{width:16px;height:16px}

  .inspired{left:250px;top:20px;width:202px;text-align:center}
  .inspired h2{font-weight:400;font-size:17.5px;line-height:22px;color:var(--blue-deep)}
  .inspired .body-text{text-align:center;margin-top:14px;font-size:8.6px;line-height:12px}
  .inspired .divider{width:130px;height:1px;background:var(--green);margin:24px auto 0}
  .inspired h3{font-weight:600;font-size:11.5px;color:var(--blue-deep);margin-top:17px;letter-spacing:.2px}
  .inspired .link{font-size:10px;line-height:14px;color:#222;margin-top:9px}
  .site{top:469px;display:flex;align-items:center;gap:5px;color:#fff;font-size:10.5px;font-weight:600}
  .site svg{width:8px;height:8px}
  .site--front{left:263px}

  .cover-title{left:496px;top:20px;font-size:25px;font-weight:600;color:var(--blue-deep);white-space:nowrap}
  .cover-title span{color:var(--green)}
  .meet{right:22px;top:433px;text-align:right;color:#fff}
  .meet strong{display:block;font-family:"Montserrat",sans-serif;font-weight:800;font-size:31px;line-height:34px}
  .meet small{display:block;font-family:"Montserrat",sans-serif;font-weight:700;font-size:10.3px;margin-top:3px;white-space:nowrap}

  /* inside sheet */
  .section-head{line-height:1}
  .section-head .kicker{display:block;font-family:"Montserrat",sans-serif;font-weight:700;font-size:15px;color:var(--blue)}
  .section-head .main{display:block;font-family:"Montserrat",sans-serif;font-weight:800;font-size:21px;color:var(--blue-deep);margin-top:3px}
  .education{left:259px;top:25px;width:196px}
  .education .body-text{margin-top:12px}
  .signature{left:259px;top:336px;width:196px;text-align:right}
  .signature .name{display:block;font-weight:300;font-size:15px;line-height:18px;color:var(--blue);text-align:left}
  .signature .cred{display:block;font-family:"Montserrat",sans-serif;font-weight:800;font-size:17px;color:var(--blue);margin-top:4px}
  .outside{left:493px;top:25px;width:195px}
  .outside .body-text{margin-top:12px;line-height:11px}
  .outside .body-text p+p{margin-top:8px}
  .site--inside{left:263px}
</style>
</head>
<body>

<!-- Outside of the brochure -->
<section class="sheet sheet--outside">
  <svg class="sheet-art" viewBox="0 0 700 496">
    <defs>
      <linearGradient id="faintFace" x1="0" y1="0" x2="1" y2="0">
        <stop offset="0" stop-color="#e9e6e4"/><stop offset="1" stop-color="#f6f4f3"/>
      </linearGradient>
      <linearGradient id="doctorPhoto" x1="0" y1="0" x2="0" y2="1">
        <stop offset="0" stop-color="#8a7a73"/><stop offset=".35" stop-color="var(--photo-skin)"/><stop offset=".55" stop-color="var(--photo-navy)"/><stop offset="1" stop-color="#1e2b47"/>
      </linearGradient>
      <linearGradient id="clinicPhoto" x1="0" y1="0" x2="1" y2="1">
        <stop offset="0" stop-color="#e8eef3"/><stop offset=".5" stop-color="#9fc3e4"/><stop offset="1" stop-color="#3a6fc1"/>
      </linearGradient>
      <clipPath id="cutDoctor"><path d="M468 78 C540 60 620 55 700 70 L700 380 C640 410 560 430 468 420 Z"/></clipPath>
    </defs>
    <rect x="234" y="0" width="234" height="496" fill="url(#faintFace)" role="img" aria-label="Faded photo of a smiling patient"/>
    <rect x="468" y="60" width="232" height="380" fill="url(#doctorPhoto)" clip-path="url(#cutDoctor)" role="img" aria-label="Photo of Dr. Marlon Duque in navy scrubs with a stethoscope"/>
    <path d="M468 92 C540 72 620 62 700 60 L700 82 C620 80 540 86 468 102 Z" fill="var(--green-soft)"/>
    <path d="M560 80 C610 68 660 64 700 64 L700 100 C660 88 610 82 560 80 Z" fill="var(--blue)"/>
    <path d="M0 285 C90 330 170 395 290 430 C420 468 560 430 700 370 L700 496 L0 496 Z" fill="var(--green)"/>
    <path d="M0 310 C90 350 170 410 290 442 C420 478 560 445 700 385 L700 496 L0 496 Z" fill="var(--blue)"/>
    <circle cx="120" cy="339" r="98" fill="var(--green)"/>
    <circle cx="120" cy="339" r="92" fill="url(#clinicPhoto)" role="img" aria-label="Photo of a dentist examining a patient"/>
  </svg>

  <div class="block memberships">
    <h2>Association Memberships</h2>
    <p class="intro">In addition to his academic credentials, Dr. Marlon Duque is a member of several associations:</p>
    <ul>
      <li><svg viewBox="0 0 10 10"><path d="M1 5.5 L4 8.5 L9 1.5" fill="none" stroke="#333" stroke-width="1.4"/></svg>The Fenwick Board of Oral Practitioners of Ontario (FBOPO)</li>
      <li><svg viewBox="0 0 10 10"><path d="M1 5.5 L4 8.5 L9 1.5" fill="none" stroke="#333" stroke-width="1.4"/></svg>Dental Meridian Guild of Oral Sleep Care (MGOSC)</li>
      <li><svg viewBox="0 0 10 10"><path d="M1 5.5 L4 8.5 L9 1.5" fill="none" stroke="#333" stroke-width="1.4"/></svg>Northern Circle of Oral Calm Care (NCOCC)</li>
      <li><svg viewBox="0 0 10 10"><path d="M1 5.5 L4 8.5 L9 1.5" fill="none" stroke="#333" stroke-width="1.4"/></svg>Pellham Dental Alliance (PDA)</li>
    </ul>
  </div>

  <div class="block phone">
    <svg viewBox="0 0 20 20"><circle cx="10" cy="10" r="8.6" fill="none" stroke="#fff" stroke-width="1.6"/><path d="M7 5.5 L8.6 5.5 L9.3 8 L8.2 9 C8.8 10.4 9.7 11.3 11 11.9 L12 10.8 L14.5 11.5 L14.5 13.1 C10 13.6 6.4 10 7 5.5 Z" fill="#fff"/></svg>
    555-014-2290
  </div>

  <div class="block inspired">
    <h2>Inspired to<br>Become a Dentist</h2>
    <div class="body-text">
      <p>As a child, Dr. Marlon Duque always felt stressed whenever he had to see a dentist. He knew that he wanted to become a dentist to help put patients completely at ease while they experienced quality dental care.</p>
      <p>He is passionate about giving patients the healthy, beautiful smiles they deserve. “I find it fulfilling when I can see my patients’ beautiful smiles and how they can finally appreciate the joy of eating with a healthy set of teeth. However, what I love most about my job is the ability to provide a stress-free and comfortable experience at the dentist’s office, particularly for children, through sedation and general anesthesia.”</p>
    </div>
    <div class="divider"></div>
    <h3>ALL YOU NEED TO KNOW HERE:</h3>
    <p class="link">http://www.calmchairhub.example<br>/what-is-calm-chair-care</p>
  </div>

  <div class="block site site--front">
    <svg viewBox="0 0 10 10"><circle cx="5" cy="5" r="4.2" fill="none" stroke="#fff"/><ellipse cx="5" cy="5" rx="1.8" ry="4.2" fill="none" stroke="#fff"/><path d="M1 5 H9" stroke="#fff"/></svg>
    www.calmchairdental.example
  </div>

  <h1 class="block cover-title">Sleep <span>Dentistry</span></h1>
  <div class="block meet">
    <strong>MEET</strong>
    <small>DR. ROEL BENET MARLON DUQUE, DDS</small>
  </div>
</section>

<!-- Inside of the brochure -->
<section class="sheet sheet--inside">
  <svg class="sheet-art" viewBox="0 0 700 496">
    <defs>
      <linearGradient id="doctorPortrait" x1="0" y1="0" x2="1" y2="0">
        <stop offset="0" stop-color="#6f7d92"/><stop offset=".45" stop-color="var(--photo-navy)"/><stop offset=".85" stop-color="#c9cdd6"/><stop offset="1" stop-color="#f2f3f5"/>
      </linearGradient>
      <linearGradient id="faintRoom" x1="0" y1="0" x2="1" y2="0">
        <stop offset="0" stop-color="#f4f4f5"/><stop offset="1" stop-color="#e9e7e6"/>
      </linearGradient>
      <linearGradient id="nursePhoto" x1="0" y1="0" x2="1" y2="1">
        <stop offset="0" stop-color="#eef1f4"/><stop offset=".55" stop-color="#b9c6d6"/><stop offset="1" stop-color="#26407a"/>
      </linearGradient>
      <radialGradient id="smilePhoto" cx=".5" cy=".45" r=".6">
        <stop offset="0" stop-color="#f3dccd"/><stop offset="1" stop-color="#d9bfae"/>
      </radialGradient>
    </defs>
    <rect x="234" y="0" width="466" height="496" fill="url(#faintRoom)" role="img" aria-label="Faded photo of a smiling patient in the dental chair"/>
    <rect x="0" y="0" width="250" height="496" fill="url(#doctorPortrait)" role="img" aria-label="Portrait of Dr. Marlon Duque smiling in scrubs"/>
    <path d="M0 380 C150 420 300 450 460 440 C570 432 640 415 700 395 L700 496 L0 496 Z" fill="var(--blue)"/>
    <path d="M0 402 C150 438 300 462 460 452 C570 444 640 430 700 412 L700 496 L0 496 Z" fill="var(--green)"/>
    <path d="M0 430 C150 460 300 478 460 472 C570 466 640 458 700 448 L700 496 L0 496 Z" fill="var(--green-soft)" opacity=".55"/>
    <circle cx="120" cy="374" r="98" fill="var(--blue)"/>
    <circle cx="120" cy="374" r="92" fill="url(#nursePhoto)" role="img" aria-label="Photo of a dental assistant treating a young patient"/>
    <circle cx="628" cy="430" r="58" fill="var(--blue)"/>
    <circle cx="628" cy="430" r="53" fill="url(#smilePhoto)" role="img" aria-label="Photo of a smiling woman with healthy teeth"/>
  </svg>

  <div class="block education">
    <h2 class="section-head"><span class="kicker">EDUCATIONAL</span><span class="main">ACHIEVEMENTS</span></h2>
    <div class="body-text">
      <p>Before becoming a dentist, Dr. Marlon Duque earned his undergraduate degree at the Northvale Institute of Arts where he received a Bachelor of Medical Science Honor Specialization degree with distinction in biochemistry. He then completed his Doctor of Dental Surgery degree with honors at the Kestrel Bay College. While there, he received the Linnet Orr Award in his class for outstanding achievement in anesthesia. He then pursued his three-year residency as well as a master’s degree in dental anesthesia at the Kestrel Bay College.</p>
      <p>So he can provide his patients with the latest in dentistry, Dr. Marlon Duque enjoys pursuing additional knowledge, particularly in the areas of dental anesthesia as well as advanced technologies in dentistry. He is currently part of the Bright Arc study circle and has enrolled in the Core Anchor Short- Fellowship Course. He also serves as a clinical instructor at the Halvex Wing at the Kestrel Bay College.</p>
    </div>
  </div>

  <div class="block signature">
    <span class="name">DR. ROEL BENET<br>MARLON DUQUE</span>
    <span class="cred">DDS</span>
  </div>

  <div class="block outside">
    <h2 class="section-head"><span class="kicker">OUTSIDE</span><span class="main">THE PRACTICE</span></h2>
    <div class="body-text">
      <p>When he’s not at the practice, Dr. Marlon Duque enjoys spending time with his wife Dorla and their two poodles Pippa and Bramble, who are spoiled rotten! “Dorla and I love taking our dogs out on hikes and to the dog park on weekends. I also enjoy a wide range of activities from model building and playing the piano to soccer, gym and archery.” He stays fit by working out at the local Fitwell gym, and he likes to walk in Marrow Creek Park and Ashbury Field Park.</p>
      <p>Dr. Marlon Duque considers himself to be a kid at heart. He is a big fan of superheroes and animated movies. “I get really excited about any upcoming superhero or Vellum Spark movies. Till this day, I still collect superhero toy figures.”</p>
      <p>He supports the BrightWard Fund as well as the Lakeshore League for Animal Welfare and Rescue (LLAWR).</p>
      <p>Experience outstanding dental care with our highly skilled dentist. Contact us today to schedule an appointment with Dr. Marlon Duque! He speaks English, Cantonese, and Mandarin.</p>
    </div>
  </div>

  <div class="block site site--inside">
    <svg viewBox="0 0 10 10"><circle cx="5" cy="5" r="4.2" fill="none" stroke="#fff"/><ellipse cx="5" cy="5" rx="1.8" ry="4.2" fill="none" stroke="#fff"/><path d="M1 5 H9" stroke="#fff"/></svg>
    www.calmchairdental.example
  </div>
</section>

</body>
</html>
```